2 sided flyer for Insurance Servics

Would like a flyer that talks about who we are, our services, and our process. Attaching relevant information, as well as our Logo and other logos for a few larger insurance carriers that we have access to.

Target Market(s)

Financial Advisors and Insurance Agents

Industry/Entity Type

Finance and Insurance

Colors
0054AA
0677BA
7BADD7
CADEEF
E8F1F8
F0912C
F2A743
F7CA91
FBE8D2
FDF5EE

Requirements
Must have
• Lists, bullet points, pictures, and logos uploaded

```html
<!DOCTYPE html>
<html lang="en">
<head>
<meta charset="utf-8">
<title>Harborline Brokerage Partners – Two-Sided Flyer</title>
<link href="https://fonts.googleapis.com/css2?family=Montserrat:wght@600;700;800;900&family=Open+Sans:wght@400;600;700&display=swap" rel="stylesheet">
<style>
  :root{
    --navy:#0b2a6b;
    --blue:#0054AA;
    --blue-mid:#0677BA;
    --blue-soft:#7BADD7;
    --blue-pale:#CADEEF;
    --blue-mist:#E8F1F8;
    --orange:#F0912C;
    --gold:#F2A743;
    --peach:#F7CA91;
    --cream:#FBE8D2;
    --ivory:#FDF5EE;
    --ink:#1d2a3f;
    --grey:#4f5a6b;
    --white:#ffffff;
    --backdrop:#eef1f5;
  }
  *{box-sizing:border-box;margin:0;padding:0}
  html,body{width:816px;height:1200px;overflow:hidden;background:var(--backdrop)}
  body{font-family:"Open Sans",Arial,sans-serif;color:var(--ink);position:relative}

  /* sheet placement: letter pages built at 816x1056, shown at reduced scale */
  .sheet{position:absolute;left:181px;width:453px;height:586px;box-shadow:0 4px 14px rgba(11,42,107,.18);overflow:hidden}
  .sheet-front{top:7px}
  .sheet-back{top:607px}
  .page{position:absolute;left:0;top:0;width:816px;height:1056px;background:var(--white);transform:scale(.555);transform-origin:0 0;overflow:hidden}

  .display{font-family:"Montserrat",Arial,sans-serif;text-transform:uppercase}
  .section-title{font-family:"Montserrat",Arial,sans-serif;font-weight:800;font-size:20px;color:var(--navy);text-transform:uppercase;letter-spacing:.4px}

  /* ---------- FRONT ---------- */
  .hero{position:absolute;left:0;top:0;width:816px;height:360px;display:flex;background:var(--navy)}
  .hero-panel{width:390px;height:360px;padding:28px 36px;position:relative}
  .brand{display:flex;align-items:center;gap:10px}
  .brand-mark{width:46px;height:46px;background:var(--white)}
  .brand-name{font-family:"Montserrat",Arial,sans-serif;font-weight:800;font-size:14px;line-height:1.15;color:var(--white);text-transform:uppercase}
  .hero-title{margin-top:40px;font-weight:900;color:var(--white);line-height:1.05}
  .hero-title .line-sm{display:block;font-size:26px}
  .hero-title .line-accent{display:block;font-size:40px;margin-top:2px}
  .hero-title .line-gold{display:block;font-size:40px;color:var(--gold)}
  .hero-photo{flex:1;height:360px;background:linear-gradient(135deg,#dfe5ec 0%,#a4b1c2 45%,#4a5c78 100%)}
  .hero-strip{position:absolute;left:0;top:360px;width:816px;height:8px;background:var(--gold)}

  .about{position:absolute;left:36px;top:390px;width:744px}
  .about p{margin-top:8px;font-size:12px;line-height:1.55;color:var(--grey)}

  .why{position:absolute;left:36px;top:518px;width:744px}
  .why-list{list-style:none;margin-top:12px;display:flex;flex-direction:column;gap:11px}
  .why-item{display:flex;gap:14px;align-items:flex-start}
  .why-icon{flex:none;width:46px;height:46px;background:var(--blue);display:flex;align-items:center;justify-content:center;border-radius:4px}
  .why-body{flex:1}
  .why-head{display:block;background:var(--gold);color:var(--navy);font-family:"Montserrat",Arial,sans-serif;font-weight:700;font-size:12.5px;padding:4px 12px}
  .why-text{margin-top:5px;font-size:11px;line-height:1.5;color:var(--grey)}

  .carriers{position:absolute;left:36px;top:906px;width:744px;display:flex;justify-content:space-between;align-items:center}
  .carrier-badge{width:110px;height:42px;background:var(--blue-mist);border:1px solid var(--blue-pale);border-radius:4px}

  /* shared footer */
  .footer{position:absolute;left:0;bottom:0;width:816px;height:58px;background:var(--navy);border-top:5px solid var(--gold);display:flex;align-items:center;justify-content:space-between;padding:0 36px;color:var(--white);font-size:12px;font-weight:600}
  .contact{display:flex;align-items:center;gap:8px}
  .contact svg{flex:none}

  /* ---------- BACK ---------- */
  .band{position:absolute;left:0;width:816px;height:46px;background:var(--navy);display:flex;align-items:center;padding:0 36px;color:var(--white);font-family:"Montserrat",Arial,sans-serif;font-weight:800;font-size:19px;text-transform:uppercase;letter-spacing:.5px}
  .band::after{content:"";width:60px;height:4px;background:var(--gold);margin-left:14px}
  .band-top{top:0}
  .band-process{top:724px}

  .col{position:absolute;top:66px;width:360px}
  .col-left{left:36px}
  .col-right{left:420px}
  .col-head{font-family:"Montserrat",Arial,sans-serif;font-weight:800;font-size:16px;color:var(--navy);text-transform:uppercase;padding-bottom:5px;border-bottom:3px solid var(--orange);display:inline-block}
  .col-intro{margin-top:8px;font-size:10.5px;line-height:1.5;color:var(--grey)}
  .ticks{list-style:none;margin-top:8px;display:flex;flex-direction:column;gap:6px}
  .tick{display:flex;gap:8px;font-size:10.5px;line-height:1.45;color:var(--grey)}
  .tick svg{flex:none;margin-top:2px}
  .tick b{color:var(--navy);font-weight:700}
  .col-gap{margin-top:18px}

  .service{padding:7px 0 7px 12px;border-left:3px solid var(--blue-soft);margin-bottom:8px}
  .service h3{font-family:"Montserrat",Arial,sans-serif;font-weight:700;font-size:12px;color:var(--blue)}
  .service p{margin-top:3px;font-size:10.3px;line-height:1.45;color:var(--grey)}
  .service-feature{background:var(--gold);border-left:3px solid var(--orange);padding:9px 12px}
  .service-feature h3{color:var(--navy)}
  .service-feature p{color:var(--navy)}

  .process{position:absolute;left:36px;top:790px;width:744px;display:flex;align-items:stretch;justify-content:space-between}
  .step{width:128px;background:var(--blue-mist);border-top:4px solid var(--blue);padding:10px 10px 12px;text-align:center}
  .step-num{width:30px;height:30px;border-radius:50%;background:var(--blue);color:var(--white);font-family:"Montserrat",Arial,sans-serif;font-weight:800;font-size:13px;display:flex;align-items:center;justify-content:center;margin:0 auto}
  .step h4{margin-top:7px;font-family:"Montserrat",Arial,sans-serif;font-weight:700;font-size:11.5px;color:var(--navy)}
  .step p{margin-top:4px;font-size:9.8px;line-height:1.4;color:var(--grey)}
  .step-arrow{display:flex;align-items:center}
</style>
</head>
<body>

<!-- FRONT SIDE -->
<div class="sheet sheet-front">
<div class="page">
  <header class="hero">
    <div class="hero-panel">
      <div class="brand">
        <span class="brand-mark"></span>
        <span class="brand-name">Harborline<br>Brokerage<br>Partners</span>
      </div>
      <h1 class="hero-title display">
        <span class="line-sm">Full-Service</span>
        <span class="line-sm">Life Insurance</span>
        <span class="line-accent">Brokerage</span>
        <span class="line-gold">General Agency</span>
      </h1>
    </div>
    <div class="hero-photo" role="img" aria-label="Photo of two business advisors in suits meeting at a desk"></div>
  </header>
  <div class="hero-strip"></div>

  <section class="about">
    <h2 class="section-title">About Us</h2>
    <p>Harborline Brokerage Partners is an independent brokerage general agency serving financial advisors and insurance agents nationwide. We combine deep case design experience with access to leading life carriers, helping you deliver the right coverage to every client. From first quote to final policy delivery, our team works alongside you so you can focus on growing your practice.</p>
  </section>

  <section class="why">
    <h2 class="section-title">Why HBP?</h2>
    <ul class="why-list">
      <li class="why-item">
        <span class="why-icon"><svg width="24" height="24" viewBox="0 0 24 24" fill="none" stroke="#fff" stroke-width="2.4" stroke-linecap="round" stroke-linejoin="round"><path d="M4 12l5 5L20 6"/></svg></span>
        <div class="why-body"><span class="why-head">Independent &amp; Advisor-Focused</span>
        <p class="why-text">We are not tied to one carrier, so every recommendation is built around your client's needs and long-term goals.</p></div>
      </li>
      <li class="why-item">
        <span class="why-icon"><svg width="24" height="24" viewBox="0 0 24 24" fill="none" stroke="#fff" stroke-width="2.4" stroke-linecap="round" stroke-linejoin="round"><path d="M4 12h14M13 6l6 6-6 6"/></svg></span>
        <div class="why-body"><span class="why-head">Access to Top-Rated Carriers</span>
        <p class="why-text">Compare products and pricing across a broad panel of highly rated life insurance companies in one place.</p></div>
      </li>
      <li class="why-item">
        <span class="why-icon"><svg width="24" height="24" viewBox="0 0 24 24" fill="none" stroke="#fff" stroke-width="2.4" stroke-linecap="round" stroke-linejoin="round"><path d="M4 12l5 5L20 6"/></svg></span>
        <div class="why-body"><span class="why-head">Expert Case Design &amp; Underwriting</span>
        <p class="why-text">Our specialists review every case, advocate with underwriters and help secure the best possible offer.</p></div>
      </li>
      <li class="why-item">
        <span class="why-icon"><svg width="24" height="24" viewBox="0 0 24 24" fill="none" stroke="#fff" stroke-width="2.4" stroke-linecap="round" stroke-linejoin="round"><path d="M4 12h14M13 6l6 6-6 6"/></svg></span>
        <div class="why-body"><span class="why-head">Dedicated Concierge Support</span>
        <p class="why-text">A single point of contact keeps your cases moving, with status updates from application to delivery.</p></div>
      </li>
      <li class="why-item">
        <span class="why-icon"><svg width="24" height="24" viewBox="0 0 24 24" fill="none" stroke="#fff" stroke-width="2.4" stroke-linecap="round" stroke-linejoin="round"><path d="M4 12l5 5L20 6"/></svg></span>
        <div class="why-body"><span class="why-head">Sales &amp; Marketing Resources</span>
        <p class="why-text">Point-of-sale tools, training and client materials designed to help you open more conversations.</p></div>
      </li>
    </ul>
  </section>

  <div class="carriers" aria-label="Partner carriers">
    <span class="carrier-badge"></span><span class="carrier-badge"></span><span class="carrier-badge"></span>
    <span class="carrier-badge"></span><span class="carrier-badge"></span><span class="carrier-badge"></span>
  </div>

  <footer class="footer">
    <span class="contact"><svg width="15" height="15" viewBox="0 0 24 24" fill="#F2A743"><path d="M6.6 10.8a15.1 15.1 0 006.6 6.6l2.2-2.2a1 1 0 011-.25 11.4 11.4 0 003.6.57 1 1 0 011 1V20a1 1 0 01-1 1A17 17 0 013 4a1 1 0 011-1h3.5a1 1 0 011 1c0 1.25.2 2.45.57 3.6a1 1 0 01-.25 1z"/></svg>(555) 214-7380</span>
    <span class="contact"><svg width="15" height="15" viewBox="0 0 24 24" fill="none" stroke="#F2A743" stroke-width="2"><circle cx="12" cy="12" r="9"/><path d="M3 12h18M12 3c3 3.5 3 14.5 0 18M12 3c-3 3.5-3 14.5 0 18"/></svg>harborlinepartners.com</span>
    <span class="contact"><svg width="13" height="17" viewBox="0 0 24 30" fill="#F2A743"><path d="M12 0a10 10 0 00-10 10c0 7.5 10 20 10 20s10-12.5 10-20A10 10 0 0012 0zm0 14a4 4 0 110-8 4 4 0 010 8z"/></svg>410 Keystone Avenue, Suite 220, Riverton, ST 40012</span>
  </footer>
</div>
</div>

<!-- BACK SIDE -->
<div class="sheet sheet-back">
<div class="page">
  <div class="band band-top">Our Services</div>

  <div class="col col-left">
    <h2 class="col-head">Our Point of Sale Strategists</h2>
    <p class="col-intro">Experienced strategists partner with you before, during and after the sale to design plans that fit each client and close with confidence.</p>
    <ul class="ticks">
      <li class="tick"><svg width="12" height="12" viewBox="0 0 24 24" fill="none" stroke="#F0912C" stroke-width="3.5" stroke-linecap="round" stroke-linejoin="round"><path d="M4 12l5 5L20 6"/></svg><span><b>Case Design:</b> tailored product and funding recommendations for each client.</span></li>
      <li class="tick"><svg width="12" height="12" viewBox="0 0 24 24" fill="none" stroke="#F0912C" stroke-width="3.5" stroke-linecap="round" stroke-linejoin="round"><path d="M4 12l5 5L20 6"/></svg><span><b>Illustrations:</b> side-by-side carrier comparisons delivered quickly.</span></li>
      <li class="tick"><svg width="12" height="12" viewBox="0 0 24 24" fill="none" stroke="#F0912C" stroke-width="3.5" stroke-linecap="round" stroke-linejoin="round"><path d="M4 12l5 5L20 6"/></svg><span><b>Joint Work:</b> support on client calls and meetings when you need it.</span></li>
      <li class="tick"><svg width="12" height="12" viewBox="0 0 24 24" fill="none" stroke="#F0912C" stroke-width="3.5" stroke-linecap="round" stroke-linejoin="round"><path d="M4 12l5 5L20 6"/></svg><span><b>Advanced Markets:</b> estate, business and executive benefit planning.</span></li>
      <li class="tick"><svg width="12" height="12" viewBox="0 0 24 24" fill="none" stroke="#F0912C" stroke-width="3.5" stroke-linecap="round" stroke-linejoin="round"><path d="M4 12l5 5L20 6"/></svg><span><b>Policy Reviews:</b> in-force audits that uncover new opportunities.</span></li>
    </ul>

    <h2 class="col-head col-gap">Our Concierge Service Team</h2>
    <p class="col-intro">Our concierge team handles the details so your cases move from application to placement smoothly and on time.</p>
    <ul class="ticks">
      <li class="tick"><svg width="12" height="12" viewBox="0 0 24 24" fill="none" stroke="#F0912C" stroke-width="3.5" stroke-linecap="round" stroke-linejoin="round"><path d="M4 12l5 5L20 6"/></svg><span><b>New Business:</b> application review and submission support.</span></li>
      <li class="tick"><svg width="12" height="12" viewBox="0 0 24 24" fill="none" stroke="#F0912C" stroke-width="3.5" stroke-linecap="round" stroke-linejoin="round"><path d="M4 12l5 5L20 6"/></svg><span><b>Underwriting Advocacy:</b> we push for the best rating possible.</span></li>
      <li class="tick"><svg width="12" height="12" viewBox="0 0 24 24" fill="none" stroke="#F0912C" stroke-width="3.5" stroke-linecap="round" stroke-linejoin="round"><path d="M4 12l5 5L20 6"/></svg><span><b>Case Tracking:</b> regular status updates and requirement follow-up.</span></li>
      <li class="tick"><svg width="12" height="12" viewBox="0 0 24 24" fill="none" stroke="#F0912C" stroke-width="3.5" stroke-linecap="round" stroke-linejoin="round"><path d="M4 12l5 5L20 6"/></svg><span><b>Contracting:</b> fast appointments with our carrier partners.</span></li>
      <li class="tick"><svg width="12" height="12" viewBox="0 0 24 24" fill="none" stroke="#F0912C" stroke-width="3.5" stroke-linecap="round" stroke-linejoin="round"><path d="M4 12l5 5L20 6"/></svg><span><b>Policy Delivery:</b> coordinated placement and commission support.</span></li>
    </ul>
  </div>

  <div class="col col-right">
    <div class="service"><h3>Term Life Insurance</h3><p>Affordable protection for set periods, with conversion options across many carriers.</p></div>
    <div class="service"><h3>Universal Life</h3><p>Flexible premiums and lasting coverage for changing client needs.</p></div>
    <div class="service"><h3>Indexed Universal Life</h3><p>Cash value growth potential linked to market indexes with downside protection.</p></div>
    <div class="service service-feature"><h3>Whole Life Insurance</h3><p>Guaranteed lifetime coverage with steady cash value growth and potential dividends.</p></div>
    <div class="service"><h3>Survivorship Life</h3><p>Second-to-die coverage built for estate and legacy planning.</p></div>
    <div class="service"><h3>Long-Term Care &amp; Hybrid Plans</h3><p>Life and care benefits combined to protect savings and independence.</p></div>
    <div class="service"><h3>Disability Income</h3><p>Income protection for professionals and business owners.</p></div>
    <div class="service"><h3>Business Planning</h3><p>Buy-sell, key person and executive benefit solutions.</p></div>
    <div class="service"><h3>Annuities</h3><p>Fixed and indexed options for retirement income.</p></div>
  </div>

  <div class="band band-process">Our Process</div>
  <div class="process">
    <div class="step"><span class="step-num">1</span><h4>Consult</h4><p>Share your client's goals and case details.</p></div>
    <div class="step-arrow"><svg width="16" height="16" viewBox="0 0 24 24" fill="none" stroke="#F0912C" stroke-width="3" stroke-linecap="round" stroke-linejoin="round"><path d="M4 12h14M13 6l6 6-6 6"/></svg></div>
    <div class="step"><span class="step-num">2</span><h4>Design</h4><p>We shop carriers and build the right plan.</p></div>
    <div class="step-arrow"><svg width="16" height="16" viewBox="0 0 24 24" fill="none" stroke="#F0912C" stroke-width="3" stroke-linecap="round" stroke-linejoin="round"><path d="M4 12h14M13 6l6 6-6 6"/></svg></div>
    <div class="step"><span class="step-num">3</span><h4>Submit</h4><p>Our team prepares and submits the application.</p></div>
    <div class="step-arrow"><svg width="16" height="16" viewBox="0 0 24 24" fill="none" stroke="#F0912C" stroke-width="3" stroke-linecap="round" stroke-linejoin="round"><path d="M4 12h14M13 6l6 6-6 6"/></svg></div>
    <div class="step"><span class="step-num">4</span><h4>Underwrite</h4><p>We advocate and track every requirement.</p></div>
    <div class="step-arrow"><svg width="16" height="16" viewBox="0 0 24 24" fill="none" stroke="#F0912C" stroke-width="3" stroke-linecap="round" stroke-linejoin="round"><path d="M4 12h14M13 6l6 6-6 6"/></svg></div>
    <div class="step"><span class="step-num">5</span><h4>Deliver</h4><p>Policy placed and your client protected.</p></div>
  </div>

  <footer class="footer">
    <span class="contact"><svg width="15" height="15" viewBox="0 0 24 24" fill="#F2A743"><path d="M6.6 10.8a15.1 15.1 0 006.6 6.6l2.2-2.2a1 1 0 011-.25 11.4 11.4 0 003.6.57 1 1 0 011 1V20a1 1 0 01-1 1A17 17 0 013 4a1 1 0 011-1h3.5a1 1 0 011 1c0 1.25.2 2.45.57 3.6a1 1 0 01-.25 1z"/></svg>(555) 214-7380</span>
    <span class="contact"><svg width="15" height="15" viewBox="0 0 24 24" fill="none" stroke="#F2A743" stroke-width="2"><circle cx="12" cy="12" r="9"/><path d="M3 12h18M12 3c3 3.5 3 14.5 0 18M12 3c-3 3.5-3 14.5 0 18"/></svg>harborlinepartners.com</span>
    <span class="contact"><svg width="13" height="17" viewBox="0 0 24 30" fill="#F2A743"><path d="M12 0a10 10 0 00-10 10c0 7.5 10 20 10 20s10-12.5 10-20A10 10 0 0012 0zm0 14a4 4 0 110-8 4 4 0 010 8z"/></svg>410 Keystone Avenue, Suite 220, Riverton, ST 40012</span>
  </footer>
</div>
</div>

</body>
</html>
```